Implant Denture Brochure

I would like to make a brochure to advertise implant dentures. This is for my dental clinic. I would like there to be some info about different implant denture options and advertise general cost. I like to use blue as a color and white. I may want to add or remove info based on the layout. Images of dentures with implants but no real photos just drawings or educational images. Real images of people smiling with dentures.

Upper
1. Implants for Upper Denture Implant Supported Removable $10,000 - $12,000 ( Includes fee for extraction of remaining upper teeth, in office sedation fees, Implant placement and necessary surgery of at least 4 implants, Does not include denture)
2. Upper Denture Implant Supported Fixed Bridge (Zirconia) $25,000 (Includes fee for extraction of all upper teeth, in office sedation fee, Implant placement and necessary surgery of at least 4 implants, includes temporary denture, and final denture)

Lower
1. Implants for Removable Lower Denture Implant Retained $5,000 - $7,000 (Includes fee for extraction of remaining lower teeth, in office sedation fees, Implant placement and necessary surgery of at least 2 implants, Does not include denture)

2. Implants for Removable Lower Denture Implant Supported $10,000 - $12,000 (Includes fee for extraction of remaining lower teeth, in office sedation fees, Implant placement and necessary surgery of at least 4 implants, Does not include denture)

3. Lower Denture Implant Supported Fixed Bridge (Zirconia) $25,000 (Includes fee for extraction of all upper teeth, in office sedation fee, Implant placement and necessary surgery of at least 4 implants, includes temporary denture, and final denture)

Copper Ridge Dental
#7 - 815 Lark Blvd N.
Copper Ridge, Alberta

```html
<!DOCTYPE html>
<html lang="en">
<head>
<meta charset="utf-8">
<title>Copper Ridge Dental – Implant Denture Brochure</title>
<link href="https://fonts.googleapis.com/css2?family=Oswald:wght@500;600;700&family=Archivo:wght@400;600;700&display=swap" rel="stylesheet">
<style>
  :root {
    --backdrop: #c9cbd0;
    --paper: #ffffff;
    --panel-grey: #ececef;
    --navy: #2a1a7c;
    --brand-blue: #1a7fe3;
    --ink: #1d1d24;
    --photo-top: #e9e2dc;
    --photo-bottom: #2a6fd0;
    --art-pink: #f6b4a8;
    --sketch: #e4e4e8;
  }
  * { box-sizing: border-box; margin: 0; padding: 0; }
  html, body { width: 1200px; height: 2279px; overflow: hidden; }
  body { background: var(--backdrop); font-family: "Archivo", Arial, sans-serif; color: var(--ink); position: relative; }

  .page {
    position: absolute; left: 220px; width: 760px; height: 1075px;
    background: var(--paper); overflow: hidden;
    box-shadow: 0 18px 40px rgba(0,0,0,.18);
  }
  .page--front { top: 43px; }
  .page--back { top: 1161px; }
  .abs { position: absolute; }

  /* brand */
  .brand { left: 43px; top: 48px; display: flex; align-items: center; gap: 12px; }
  .brand__dot { width: 30px; height: 30px; border-radius: 50%; background: var(--navy); }
  .brand__name { font-family: "Oswald", sans-serif; font-weight: 600; font-size: 26px; line-height: 30px; letter-spacing: 1.5px; color: var(--navy); text-transform: uppercase; }

  .tagline {
    left: 43px; top: 170px; height: 64px; padding: 0 16px;
    background: var(--navy); color: #fff; border-radius: 4px;
    font-family: "Oswald", sans-serif; font-weight: 500; font-size: 31px;
    line-height: 64px; letter-spacing: -.5px; text-transform: uppercase;
  }
  .headline {
    left: 43px; top: 248px; width: 330px; z-index: 2;
    font-family: "Oswald", sans-serif; font-weight: 700; font-size: 60px;
    line-height: 58px; letter-spacing: -2px; color: var(--navy); text-transform: uppercase;
  }
  .section-title {
    font-family: "Oswald", sans-serif; font-weight: 500; font-size: 40px;
    color: var(--brand-blue); letter-spacing: -1.5px; text-transform: uppercase;
    border-bottom: 2px solid var(--brand-blue); line-height: 48px;
  }

  .photo {
    left: 380px; top: 23px; width: 380px; height: 545px;
    background: linear-gradient(180deg, var(--photo-top) 0%, #dcd0c6 40%, var(--photo-bottom) 75%);
  }

  .panel-grey { background: var(--panel-grey); }
  .front-panel { left: 380px; top: 490px; width: 380px; height: 585px; border-top-left-radius: 140px; border-top-right-radius: 40px; }

  .art {
    border-radius: 18px;
    background: linear-gradient(135deg, var(--art-pink) 0%, #fbe3dc 45%, var(--brand-blue) 46%, #3b95ec 100%);
  }
  .art--plain { background: linear-gradient(135deg, #f4a79b, #f9d8d0); border-radius: 40%; }
  .sketch { background: var(--sketch); border-radius: 30%; opacity: .8; }

  .item-title { font-weight: 700; font-size: 17px; line-height: 19px; color: var(--navy); letter-spacing: -.3px; }
  .item-body { font-size: 16px; line-height: 22px; letter-spacing: -.4px; color: var(--ink); }
  .price {
    height: 58px; padding: 0 17px; background: var(--navy); color: #fff; border-radius: 5px;
    font-family: "Oswald", sans-serif; font-weight: 500; font-size: 34px; line-height: 58px; letter-spacing: -1.5px;
  }

  .back-panel { left: 0; top: 0; width: 380px; height: 640px; border-bottom-right-radius: 150px; }

  .address {
    left: 452px; top: 866px; width: 256px; height: 156px; background: var(--navy);
    border-radius: 8px; padding: 8px;
  }
  .address__frame {
    width: 100%; height: 100%; border: 1.5px dashed rgba(255,255,255,.7); border-radius: 5px;
    display: flex; flex-direction: column; align-items: center; justify-content: center;
    color: #fff; font-size: 16px; line-height: 21px; text-align: center; letter-spacing: -.4px;
  }
  .address__pin { margin-bottom: 8px; }
</style>
</head>
<body>

<!-- Front: upper jaw -->
<section class="page page--front">
  <div class="abs brand">
    <span class="brand__dot"></span>
    <span class="brand__name">Copper Ridge<br>Dental</span>
  </div>

  <div class="abs sketch" style="left:300px;top:78px;width:64px;height:64px;" role="img" aria-label="Sketch of a dental implant"></div>

  <div class="abs photo" role="img" aria-label="Photo of a smiling woman holding a white tooth model in her hands"></div>

  <div class="abs tagline">We value your smile</div>
  <h1 class="abs headline">Your Copper Ridge, AB Dentist!</h1>

  <div class="abs front-panel panel-grey"></div>

  <h2 class="abs section-title" style="left:43px;top:495px;">Upper Jaw</h2>

  <!-- item: removable -->
  <div class="abs art" style="left:35px;top:565px;width:285px;height:155px;" role="img" aria-label="Illustration of an upper denture beside implant posts in a blue tooth shape"></div>
  <h3 class="abs item-title" style="left:43px;top:735px;width:280px;">Denture<br>Implant Supported<br>Removable</h3>
  <p class="abs item-body" style="left:43px;top:800px;width:285px;">Implants for Upper Denture Implant Supported Removable Includes fee for extraction of remaining upper teeth, in office sedation fees, Implant placement and necessary surgery of atleast 4 implants, Does not include denture</p>
  <div class="abs sketch" style="left:333px;top:895px;width:38px;height:60px;" role="img" aria-label="Sketch of a tooth"></div>
  <div class="abs price" style="left:35px;top:965px;">$10,000 - $12,000</div>

  <!-- item: fixed bridge -->
  <div class="abs art" style="left:415px;top:565px;width:295px;height:155px;" role="img" aria-label="Illustration of an upper denture beside a crown on an implant in a blue tooth shape"></div>
  <h3 class="abs item-title" style="left:416px;top:735px;width:280px;">Denture<br>Implant Supported<br>Fixed Bridge</h3>
  <p class="abs item-body" style="left:416px;top:800px;width:305px;">Upper Denture Implant Supported Fixed Bridge (Zirconia) Includes fee for extraction of all upper teeth, in office sedation fee, Implant placement and necessary surgery of at least 4 implants, includes temporary denture, and final denture</p>
  <div class="abs sketch" style="left:575px;top:975px;width:95px;height:80px;" role="img" aria-label="Sketch of a molar"></div>
  <div class="abs price" style="left:416px;top:965px;">$25,000</div>
</section>

<!-- Back: lower jaw -->
<section class="page page--back">
  <div class="abs back-panel panel-grey"></div>

  <h2 class="abs section-title" style="left:58px;top:45px;">Lower Jaw</h2>
  <div class="abs sketch" style="left:272px;top:75px;width:80px;height:80px;" role="img" aria-label="Sketch of a molar"></div>
  <div class="abs sketch" style="left:665px;top:10px;width:85px;height:120px;" role="img" aria-label="Sketch of a tooth"></div>

  <!-- retained -->
  <div class="abs art" style="left:50px;top:115px;width:200px;height:170px;" role="img" aria-label="Illustration of a lower denture on two implants in a blue tooth shape"></div>
  <h3 class="abs item-title" style="left:58px;top:305px;width:300px;">Removable Lower<br>Denture Implant Retained</h3>
  <p class="abs item-body" style="left:58px;top:352px;width:295px;">Implants for Removable Lower Denture Implant Retained Includes fee for extraction of remaining lower teeth, in office sedation fees, Implant placement and necessary surgery of at least 2 implants, Does not include denture)</p>
  <div class="abs price" style="left:58px;top:525px;">$5,000 - $7,000</div>

  <!-- supported -->
  <div class="abs art" style="left:440px;top:115px;width:200px;height:170px;" role="img" aria-label="Illustration of a lower denture on four implants in a blue tooth shape"></div>
  <h3 class="abs item-title" style="left:445px;top:305px;width:290px;">Removable Lower<br>Denture Implant Supported</h3>
  <p class="abs item-body" style="left:445px;top:352px;width:290px;">Implants for Removable Lower Denture Implant Supported Includes fee for extraction of remaining lower teeth, in office sedation fees, Implant placement and necessary surgery of at least 4 implants, Does not include denture)</p>
  <div class="abs price" style="left:445px;top:525px;">$10,000 - $12,000</div>

  <!-- fixed bridge -->
  <div class="abs art" style="left:250px;top:575px;width:140px;height:150px;" role="img" aria-label="Illustration of a lower fixed bridge on implants in a blue tooth shape"></div>
  <h3 class="abs item-title" style="left:58px;top:745px;width:260px;">Denture Implant<br>Supported Fixed Bridge</h3>
  <p class="abs item-body" style="left:58px;top:800px;width:305px;">Lower Denture Implant Supported Fixed Bridge (Zirconia) Includes fee for extraction of all upper teeth, in office sedation fee, Implant placement and necessary surgery of at least 4 implants, includes temporary denture, and final denture)</p>
  <div class="abs price" style="left:58px;top:965px;">$25,000</div>
  <div class="abs sketch" style="left:255px;top:980px;width:80px;height:80px;" role="img" aria-label="Sketch of dental forceps"></div>

  <div class="abs sketch" style="left:685px;top:590px;width:65px;height:80px;" role="img" aria-label="Sketch of a tooth"></div>
  <div class="abs art--plain" style="left:470px;top:680px;width:200px;height:150px;" role="img" aria-label="Illustration of a lower jaw model with a single implant and crown"></div>

  <div class="abs address">
    <div class="address__frame">
      <svg class="address__pin" width="14" height="18" viewBox="0 0 14 18" aria-hidden="true">
        <path d="M7 0C3.1 0 0 3.1 0 7c0 5.2 7 11 7 11s7-5.8 7-11c0-3.9-3.1-7-7-7z" fill="#fff"/>
        <circle cx="7" cy="7" r="2.6" fill="#2a1a7c"/>
      </svg>
      <span>Copper Ridge Dental</span>
      <span>#7 - 815 Lark Blvd N.</span>
      <span>Copper Ridge, Alberta</span>
    </div>
  </div>
</section>

</body>
</html>
```